Design website for new email startup

We are starting a company called Pingo.QZ (it will live at http://pingo.qz).

We would like the main landing page for our site designed. We have provided a very simple wireframe to help provide direction for the content it should include, but we do not expect the designers to adhere to it at all - we encourage unique ideas. There is some sample text in the wireframe - this does not have to be used, but may provide ideas.

We provide an easy way for people to manage email for a custom domain name. For example if you own "yourhouseword.example" you can point your DNS records to us and we'll make it easy to have emails addressed to your domain get forwarded to your existing email (gmail, etc). Folks running blogs, and other small sites can quickly setup email addresses for their domains and manage them in one place.

(For technical folks, we have you point your dns mx records to us, hence the name. That way all your email hits us and we can redirect it wherever you want. We make it easy to manage a single domain or a bunch of domains. Many domain registrars offer this service for a fee, and have clumsy management tools. We provide a robust simple toolset for free, as well as premium options).

The goal of the landing page is to get folks into the signup flow. The second priority flow is to have them take a look at the premium plan offerings.

We may offer the winning designer additional work for the remainder of the site design.
Updates

I've changed this project to a committed payment.  It is no longer refundable.  Thank you.

Target Market(s)

Bloggers, podcasters, designers, app developers - people who are a little tech savvy.

Industry/Entity Type

It Company

Font styles to use
Sans Serif

Colors

Designer to choose colors to be used in the design.

Requirements
Must have
• A full fidelity mockup (comp) of the landing page including the source file (psd, ai, etc).

Some sort of logo treatment for the pingo.qz brand

A call to action for signup, such as the suggested 'Get Started Here'
Nice to have
• A hip startup feel

Incorporation of the email theme

Give the impression it is simple, easy and fast

```html
<!DOCTYPE html>
<html lang="en">
<head>
<meta charset="utf-8">
<title>Pingo.QZ — Email for your domain</title>
<link href="https://fonts.googleapis.com/css2?family=Open+Sans:wght@300;400;600;700&display=swap" rel="stylesheet">
<style>
  :root{
    --header-bg:#1b1b1b;
    --tab-bg:#3f3f3f;
    --brand-orange:#d0642a;
    --brand-yellow:#f0c233;
    --quote-bg:#f3cd5d;
    --quote-mark:#d5a62c;
    --quote-text:#5a4508;
    --hero-bg:#e4eff0;
    --ink:#1f1f1f;
    --ink-soft:#444;
    --feature-title:#a0441a;
    --body-text:#555;
    --line-blue:#7fb5c8;
    --footer-bg:#2a2a2a;
  }
  *{box-sizing:border-box;margin:0;padding:0}
  html,body{width:1200px;height:938px;overflow:hidden}
  body{font-family:"Open Sans",Arial,sans-serif;background:#fff;position:relative}

  .site-header{position:absolute;left:0;top:0;width:1200px;height:104px;background:var(--header-bg)}
  .brand{position:absolute;left:140px;top:22px;height:60px;display:flex;align-items:center;gap:12px}
  .brand-dot{width:60px;height:60px;border-radius:50%;background:var(--brand-yellow)}
  .brand-name{color:var(--brand-orange);font-size:34px;font-weight:600;line-height:36px}
  .main-nav{position:absolute;left:791px;top:71px;display:flex;gap:3px}
  .main-nav a{display:block;height:33px;padding:0 9px;line-height:35px;background:var(--tab-bg);color:#fff;text-decoration:none;font-size:15px;border-radius:4px 4px 0 0}

  .hero{position:absolute;left:0;top:104px;width:1200px;height:594px;
    background:radial-gradient(ellipse 360px 300px at 900px 320px,#fff 0%,rgba(255,255,255,0) 70%),var(--hero-bg)}
  .testimonial{position:absolute;left:140px;top:28px;width:918px;height:97px;background:var(--quote-bg);border:2px solid #fff;border-radius:3px;box-shadow:0 1px 3px rgba(0,0,0,.12)}
  .quote-mark{position:absolute;color:var(--quote-mark);font-size:110px;font-weight:700;line-height:1;font-family:Georgia,serif}
  .quote-open{left:18px;top:-4px}
  .quote-close{right:18px;top:28px}
  .testimonial p{position:absolute;left:88px;right:88px;top:34px;text-align:center;color:var(--quote-text);font-size:15px;line-height:23px}
  .testimonial strong{font-weight:600}

  .headline{position:absolute;left:140px;top:222px;width:380px;font-weight:300;font-size:22.5px;line-height:30px;color:var(--ink-soft);letter-spacing:-.6px}
  .headline strong{font-weight:600;font-size:38px;color:var(--ink);letter-spacing:-.5px}
  .btn-start{position:absolute;left:140px;top:377px;width:213px;height:42px;background:var(--quote-bg);border-bottom:3px solid #c99d22;border-radius:2px;color:#3a2e0a;font-size:18px;padding-left:8px;line-height:42px;text-decoration:none}
  .btn-start b{font-weight:700}
  .btn-start .chev{position:absolute;right:12px;top:9px}

  .price-cloud{position:absolute;left:465px;top:362px;width:270px;height:95px}
  .price-label{position:absolute;font-size:13px;color:#111}
  .price-start{left:494px;top:424px}
  .price-per{left:676px;top:424px}
  .price-amount{position:absolute;left:540px;top:392px;font-size:47px;font-weight:400;color:#000;letter-spacing:-1px}
  .price-tag{position:absolute;left:664px;top:374px;width:54px;height:32px;background:#f6e7b0;transform:rotate(-12deg);font-size:13px;font-weight:700;line-height:13px;text-align:center;padding-top:3px;color:#333;border-radius:3px}

  .globe-art{position:absolute;left:756px;top:175px;width:290px;height:290px;border-radius:50%;
    background:radial-gradient(circle at 40% 35%,#4fd0f2 0%,#1c7fc6 45%,#0c2f7a 100%)}

  .divider{position:absolute;top:524px;height:1px;background:var(--line-blue)}
  .divider-left{left:195px;width:298px}
  .divider-right{left:707px;width:338px}
  .btn-plans{position:absolute;left:502px;top:499px;width:195px;height:50px;background:var(--brand-orange);border-bottom:3px solid #8e3d14;border-radius:2px;color:#fff;font-size:19px;font-weight:600;text-align:center;line-height:50px;text-decoration:none}

  .feature{position:absolute;top:746px}
  .feature-one{left:150px;width:350px}
  .feature-two{left:616px;width:450px}
  .feature-icon{position:absolute;left:0;top:2px}
  .feature h2{margin-left:57px;font-weight:400;font-size:20px;line-height:20px;color:var(--feature-title)}
  .feature-two h2{margin-left:61px}
  .feature p{margin:12px 0 0 57px;font-weight:300;font-size:13.5px;line-height:17px;color:var(--body-text)}
  .feature-two p{margin-left:60px}

  .site-footer{position:absolute;left:0;top:907px;width:1200px;height:31px;background:var(--footer-bg);color:#fff;text-align:center;font-size:13px;line-height:31px}
</style>
</head>
<body>
<header class="site-header">
  <div class="brand">
    <span class="brand-dot"></span>
    <span class="brand-name">Pingo.QZ</span>
  </div>
  <nav class="main-nav">
    <a href="#">How It Works</a>
    <a href="#">Support</a>
    <a href="#">Login</a>
  </nav>
</header>

<section class="hero">
  <blockquote class="testimonial">
    <span class="quote-mark quote-open">“</span>
    <p><strong>Lorem Ipsum is simply dummy text of the printing and typesetting industry.</strong> Lorem Ipsum has been the industry's standard dummy text ever since the <strong>1500s, when an unknown</strong> printer took.</p>
    <span class="quote-mark quote-close">”</span>
  </blockquote>

  <h1 class="headline"><strong>Choosing</strong> and registeringa great domain name is one of the first steps towards building a successful internet presence.</h1>
  <a class="btn-start" href="#">GET STARTED <b>FREE</b>
    <svg class="chev" width="22" height="22" viewBox="0 0 22 22" aria-hidden="true"><circle cx="11" cy="11" r="10" fill="none" stroke="#c99d22"/><path d="M7 9l4 4 4-4" fill="none" stroke="#a07d18" stroke-width="2"/></svg>
  </a>

  <svg class="price-cloud" viewBox="0 0 270 95" aria-hidden="true">
    <path d="M0 90 Q10 60 45 62 Q55 40 85 44 Q100 10 140 12 Q185 12 195 44 Q230 38 245 62 Q268 66 270 90 Z" fill="#fff" opacity=".9"/>
  </svg>
  <span class="price-label price-start">Start</span>
  <span class="price-amount">$3.98</span>
  <span class="price-label price-per">/mo</span>
  <span class="price-tag">30%<br>OFF</span>

  <div class="globe-art" role="img" aria-label="Illustration of a blue globe with a magnifying glass showing a web address bar"></div>

  <span class="divider divider-left"></span>
  <a class="btn-plans" href="#">COMPARE PLANS</a>
  <span class="divider divider-right"></span>
</section>

<article class="feature feature-one">
  <svg class="feature-icon" width="44" height="44" viewBox="0 0 44 44" aria-hidden="true">
    <g fill="none" stroke="#a0441a" stroke-width="3"><circle cx="22" cy="22" r="19"/><ellipse cx="22" cy="22" rx="8" ry="19"/><path d="M3 22h38M7 12h30M7 32h30"/></g>
  </svg>
  <h2>Configure your SkyShield<br>DNS to use pingo.qz</h2>
  <p>Lorem ipsum dolor sit amet, consectetur adipi-sicing elit, sed do eiusmod tempor incididunt ut labore et dolore magna aliqua. Ut enim ad minim veniam, quis nostrud. exercitation ullamco laboris nisi ut aliquip.</p>
</article>

<article class="feature feature-two">
  <svg class="feature-icon" width="48" height="46" viewBox="0 0 48 46" aria-hidden="true">
    <g fill="none" stroke="#a0441a" stroke-width="3"><circle cx="22" cy="22" r="19"/><ellipse cx="22" cy="22" rx="8" ry="19"/><path d="M3 22h38M7 12h30M7 32h30"/></g>
    <path d="M32 28h5v8h3v-5h3v5h3v10H32z" fill="#a0441a"/>
  </svg>
  <h2>Pingo.QZ with your NameHarbor domain registraton for reliable email forwarding</h2>
  <p>Lorem ipsum dolor sit amet, consectetur adipisicing elit, sed do eiusmod tempor incididunt ut labore et dolore magna aliqua. Ut enim ad minim veniam, quis nostrud. exercitation ullamco labo-ris nisi ut aliquip.</p>
</article>

<footer class="site-footer">Copyright © 2014, Pingo.QZ All Rights Reserved.</footer>
</body>
</html>
```